Commercial Refrigeration Service Company requires stylish and fresh looking flyer.

We need a flyer to hand out to new customers. It should have a photo and our branding, list all the services that are offered and our contact details.
We would like two flyers to be supplied, both identical though one offering a discount until July ( Half Price Service Fee ). The flyer should be clear, interesting and in similar colours to the branding package supplied.
Please look at our website for information about the services on offer:
www.brisko-coolworks.com.au

Target Market(s)

Cafes, bars, restaurants, pubs ect.

Font styles to use
Other font styles liked:
• Font package provided

Colors
85cae6
ffffff
333333

Requirements
Must have
• - The photo provided.
• - The company logo.
• - Similar feel to the website & business card.
• - Smooth layout and clear to understand.
Should not have
• - No clunky badges or prints.

```html
<!DOCTYPE html>
<html lang="en">
<head>
<meta charset="utf-8">
<title>Brisko Commercial Refrigeration – Flyer</title>
<link rel="stylesheet" href="https://fonts.googleapis.com/css2?family=Dosis:wght@300;400&family=Open+Sans:wght@400;600&display=swap">
<style>
  :root {
    --brand-blue: #5bc3eb;
    --brand-blue-soft: #85cae6;
    --ink: #333333;
    --paper-top: #f5f5f5;
    --paper-bottom: #e4e4e4;
    --stage: #7a7a7a;
    --icon-fill: #8a8a8c;
    --white: #ffffff;
  }
  * { margin: 0; padding: 0; box-sizing: border-box; }
  html, body { width: 1200px; height: 1146px; overflow: hidden; }
  body { background: var(--stage); position: relative; }

  .flyer {
    position: absolute; left: 212px; top: 24px;
    width: 776px; height: 1098px;
    background: linear-gradient(180deg, var(--paper-top) 45%, var(--paper-bottom) 100%);
    overflow: hidden;
    color: var(--ink);
  }
  .flyer > * { position: absolute; left: 0; width: 100%; text-align: center; }

  .hero-photo {
    top: 0; height: 368px;
    background: linear-gradient(180deg, #a9c8e4 0%, #cfdbe6 30%, #7d8187 55%, #5f6266 80%, #8c8b88 100%);
  }

  .brand-band { top: 368px; height: 154px; background: var(--brand-blue); }
  .brand-name {
    top: 418px; line-height: 54px;
    font-family: "Dosis", sans-serif; font-weight: 400;
    font-size: 46px; letter-spacing: 2px;
    color: var(--ink);
  }

  .business-line {
    top: 552px; line-height: 30px;
    font-family: "Dosis", sans-serif; font-weight: 400;
    font-size: 24px; color: var(--ink);
  }

  .offer-title {
    top: 628px; line-height: 48px;
    font-family: "Dosis", sans-serif; font-weight: 300;
    font-size: 44px; color: var(--brand-blue);
  }
  .offer-detail {
    top: 673px; line-height: 30px;
    font-family: "Dosis", sans-serif; font-weight: 300;
    font-size: 27px; color: var(--brand-blue);
  }
  .divider-dots { top: 716px; height: 12px; }

  .services-title {
    top: 752px; line-height: 30px;
    font-family: "Dosis", sans-serif; font-weight: 300;
    font-size: 27px; color: var(--brand-blue);
  }
  .services-list {
    top: 781px; line-height: 27px;
    font-family: "Dosis", sans-serif; font-weight: 400;
    font-size: 21px; color: var(--ink);
  }

  .service-icons {
    top: 858px; height: 66px;
    display: flex; justify-content: center; gap: 5px;
  }
  .service-icon {
    width: 64px; height: 64px; border-radius: 50%;
    background: var(--icon-fill); border: 2px solid var(--brand-blue);
    display: flex; align-items: center; justify-content: center;
  }
  .service-icon svg { width: 38px; height: 38px; fill: none; stroke: var(--white); stroke-width: 1.6; stroke-linecap: round; stroke-linejoin: round; }

  .footer-rule { top: 984px; height: 14px; }

  .contact-line {
    top: 1014px; line-height: 26px;
    font-family: "Open Sans", sans-serif; font-weight: 400;
    font-size: 19px; color: var(--ink);
  }
  .web-address {
    top: 1041px; line-height: 26px;
    font-family: "Open Sans", sans-serif; font-weight: 600;
    font-size: 20px; color: var(--brand-blue);
  }
</style>
</head>
<body>
  <main class="flyer">
    <div class="hero-photo" role="img" aria-label="Photo of the technician standing beside the branded service ute at a beachside car park"></div>

    <div class="brand-band"></div>
    <div class="brand-name">Brisko</div>

    <p class="business-line">Commercial Refrigeration</p>

    <h1 class="offer-title">DISCOUNT UNTIL JULY</h1>
    <p class="offer-detail">PAY ONLY HALF PRICE OF THE SERVICE FEE</p>

    <svg class="divider-dots" viewBox="0 0 776 12" aria-hidden="true">
      <g fill="none" stroke="#5bc3eb" stroke-width="1.3">
        <path d="M358 6 L362 2 L366 6 L362 10 Z"/>
        <path d="M384 6 L388 2 L392 6 L388 10 Z"/>
        <path d="M410 6 L414 2 L418 6 L414 10 Z"/>
      </g>
    </svg>

    <h2 class="services-title">SERVICES</h2>
    <p class="services-list">Commercial Refrigeration | Ice Makers | Beer Systems<br>Electrical | 24hr Service | Sales | Installation</p>

    <div class="service-icons">
      <div class="service-icon" aria-label="Refrigeration"><svg viewBox="0 0 40 40"><path d="M17 6 a3 3 0 0 1 6 0 v17 a6 6 0 1 1 -6 0 Z"/><circle cx="20" cy="28" r="2.5"/><path d="M20 12 v13 M26 9 h4 M26 13 h3 M26 17 h4"/></svg></div>
      <div class="service-icon" aria-label="Ice makers"><svg viewBox="0 0 40 40"><path d="M9 8 h22 l-3 25 h-16 Z"/><path d="M10 13 h20"/><rect x="14" y="19" width="6" height="6"/><rect x="20" y="24" width="6" height="6"/></svg></div>
      <div class="service-icon" aria-label="Beer systems"><svg viewBox="0 0 40 40"><path d="M22 6 l-6 12 M14 18 h10 v6 h-10 Z M20 24 v5 M16 29 h8 v4 h-8 Z"/><circle cx="20" cy="36" r="1"/></svg></div>
      <div class="service-icon" aria-label="Electrical"><svg viewBox="0 0 40 40"><path d="M24 5 l-11 17 h7 l-4 13 l12 -18 h-7 Z"/></svg></div>
      <div class="service-icon" aria-label="24hr service"><svg viewBox="0 0 40 40"><path d="M9 31 l13 -13 M22 18 a6 6 0 1 0 4 -8 l-3 3 l2 3 l3 -1"/><path d="M31 31 l-13 -13 M12 8 l4 4 l-3 3 l-4 -4"/></svg></div>
      <div class="service-icon" aria-label="Sales"><svg viewBox="0 0 40 40"><path d="M5 10 h5 l4 15 h18 l3 -11 h-23"/><circle cx="16" cy="30" r="2"/><circle cx="29" cy="30" r="2"/></svg></div>
      <div class="service-icon" aria-label="Installation"><svg viewBox="0 0 40 40"><path d="M8 26 l18 -18 l6 6 l-18 18 Z M12 22 l2 2 M16 18 l2 2 M20 14 l2 2"/><path d="M10 10 l20 20 l2 4 l-4 -2 l-20 -20 Z"/></svg></div>
    </div>

    <svg class="footer-rule" viewBox="0 0 776 14" aria-hidden="true">
      <g fill="none" stroke="#5bc3eb" stroke-width="1.5">
        <line x1="64" y1="7" x2="712" y2="7"/>
        <path d="M52 7 L58 1 L64 7 L58 13 Z"/>
        <path d="M712 7 L718 1 L724 7 L718 13 Z"/>
      </g>
    </svg>

    <p class="contact-line">0400 127 384 &nbsp;| Info@brisko-coolworks.com.au</p>
    <p class="web-address">www.brisko-coolworks.com.au</p>
  </main>
</body>
</html>
```